Birchline Septic Solutions

Would like to see some single sided ones but would also like to see some double sided with one sided only being the logo. Owners name is Colin Vandro. Phone number is 555-214-0387
Services are pumping, inspections, installs, and repairs

Contact Information for Business Card

555-241-0387 Colin Vandro Maplecrest, OH

```html
<!DOCTYPE html>
<html lang="en">
<head>
<meta charset="utf-8">
<title>Birchline Septic Solutions — Business Cards</title>
<link href="https://fonts.googleapis.com/css2?family=Montserrat:wght@500;600;800&display=swap" rel="stylesheet">
<style>
  :root {
    --stage: #3a3a3a;
    --card-dark: #141414;
    --card-light: #ffffff;
    --ink: #111111;
    --teal: #2bb5ad;
    --band: #151515;
    --muted: #8a8a8a;
  }
  * { box-sizing: border-box; margin: 0; padding: 0; }
  html, body { width: 1200px; height: 689px; overflow: hidden; }
  body {
    background: var(--stage);
    font-family: "Montserrat", Arial, sans-serif;
    position: relative;
  }
  .card {
    position: absolute;
    top: 190px;
    width: 540px;
    height: 309px;
    border-radius: 18px;
    overflow: hidden;
  }
  .card--back { left: 40px; background: var(--card-dark); }
  .card--front { left: 620px; background: var(--card-light); }

  .back-scene {
    position: absolute;
    inset: 0 0 0 200px;
    background:
      radial-gradient(ellipse at 75% 20%, #9a9a9a 0%, #4a4a4a 28%, transparent 55%),
      linear-gradient(180deg, #2a2a2a 0%, #1c1c1c 60%, #141414 100%);
    -webkit-mask-image: linear-gradient(90deg, transparent 0%, #000 35%);
            mask-image: linear-gradient(90deg, transparent 0%, #000 35%);
  }
  .brand {
    position: absolute;
    display: flex;
    align-items: center;
    gap: 10px;
    font-weight: 800;
    text-transform: uppercase;
    line-height: 1.1;
  }
  .brand__mark { width: 14px; height: 14px; background: var(--teal); flex: none; }
  .brand__name { font-size: 26px; letter-spacing: 1px; white-space: nowrap; }
  .card--back .brand { left: 40px; top: 112px; color: #fff; }
  .card--front .brand { left: 34px; top: 104px; color: var(--ink); }
  .card--front .brand__name { font-size: 18px; letter-spacing: 0.5px; }

  .divider {
    position: absolute;
    left: 300px; top: 40px;
    width: 1px; height: 160px;
    background: linear-gradient(180deg, transparent, var(--muted), transparent);
  }
  .contact { position: absolute; left: 326px; top: 62px; color: var(--ink); }
  .contact__name { font-size: 20px; font-weight: 800; text-transform: uppercase; margin-bottom: 20px; white-space: nowrap; }
  .contact__row { display: flex; align-items: center; gap: 9px; font-size: 14px; font-weight: 500; margin-bottom: 10px; white-space: nowrap; }
  .contact__row svg { width: 14px; height: 14px; flex: none; }

  .service-band {
    position: absolute; left: 0; right: 0; bottom: 0;
    height: 58px;
    background: var(--band);
    border-top: 4px solid var(--teal);
    display: flex; align-items: center; justify-content: center;
    gap: 12px;
    color: #fff; font-size: 13px; font-weight: 600;
    text-transform: uppercase; letter-spacing: 0.5px;
  }
  .service-band .dot { width: 6px; height: 6px; border-radius: 50%; background: var(--teal); }
</style>
</head>
<body>
  <section class="card card--back" aria-label="Card back">
    <div class="back-scene" role="img" aria-label="Dark mountain peaks and pine forest silhouette"></div>
    <div class="brand">
      <span class="brand__mark"></span>
      <span class="brand__name">Birchline<br>Septic Solutions</span>
    </div>
  </section>

  <section class="card card--front" aria-label="Card front">
    <div class="brand">
      <span class="brand__mark"></span>
      <span class="brand__name">Birchline<br>Septic Solutions</span>
    </div>
    <div class="divider"></div>
    <div class="contact">
      <p class="contact__name">Colin Vandro</p>
      <p class="contact__row">
        <svg viewBox="0 0 24 24" fill="none" stroke="#2bb5ad" stroke-width="2.4" stroke-linecap="round"><path d="M5 4h4l2 5-2.5 1.5a11 11 0 0 0 5 5L15 13l5 2v4a2 2 0 0 1-2 2A16 16 0 0 1 3 6a2 2 0 0 1 2-2z"/></svg>
        555-214-0387
      </p>
      <p class="contact__row">
        <svg viewBox="0 0 24 24" fill="#2bb5ad"><path d="M12 2a7 7 0 0 0-7 7c0 5 7 13 7 13s7-8 7-13a7 7 0 0 0-7-7zm0 9.5A2.5 2.5 0 1 1 12 6.5a2.5 2.5 0 0 1 0 5z"/></svg>
        Maplecrest, OH
      </p>
    </div>
    <div class="service-band">
      <span>Pumping</span><span class="dot"></span>
      <span>Inspections</span><span class="dot"></span>
      <span>Installs</span><span class="dot"></span>
      <span>Repairs</span>
    </div>
  </section>
</body>
</html>
```